larkforge website

commerce website to sell cookeries, brackets, mailboxes and to show off homes built. Modern Steel in design see marlo cycles web page to be like: https://www.marlocycles-demo.com/en/ sorry its bright nest hosting word press divi

must be able to add products to page

Target Market(s)

mainly western states of U.S.

Industry/Entity Type

Building Product

Coding

Coded - Design and coding required

Number of Pages Required

3 page

Font styles to use
Sans Serif

Colors

Designer to choose colors to be used in the design.

Requirements
Must have
• customers to be able to order products from page
• bright nest hosting word press divi

```html
<!DOCTYPE html>
<html lang="en">
<head>
<meta charset="utf-8">
<title>Larkforge – Outdoor Fire Pit</title>
<link rel="stylesheet" href="https://fonts.googleapis.com/css2?family=Source+Sans+3:ital,wght@0,400;0,600;0,700;1,400&display=swap">
<style>
:root{
  --navy:#4b5a86;
  --ink:#121212;
  --muted:#6a6a6a;
  --mist:#eef0f5;
  --disc:#eceef2;
  --white:#ffffff;
  --night:#2a2622;
}
*{box-sizing:border-box;margin:0;padding:0}
html,body{width:1200px;height:3532px;overflow:hidden}
body{position:relative;background:var(--white);font-family:"Source Sans 3",sans-serif;color:var(--ink)}
.abs{position:absolute}
.backdrop{left:0;top:0}
.brand{display:flex;align-items:center;gap:10px;color:var(--white);font-weight:600;font-size:26px;letter-spacing:1px}
.brand-dot{width:16px;height:16px;border-radius:50%;background:var(--white)}
.nav{left:528px;top:47px;display:flex;gap:0}
.nav a{position:absolute;white-space:nowrap;color:var(--white);font-size:12.5px;font-weight:700;text-decoration:none}
.nav-icon{width:36px;height:36px;border-radius:50%;border:1.5px solid rgba(255,255,255,.8);display:flex;align-items:center;justify-content:center}
.nav-icon span{width:26px;height:26px;border-radius:50%;background:var(--white);display:flex;align-items:center;justify-content:center}
.hero-title{left:162px;top:180px;color:var(--white);font-size:62px;font-weight:700;line-height:64px}
.hero-copy{left:162px;top:324px;color:#e2e2e2;font-size:13.5px;line-height:21px;width:440px}
.btn{display:flex;align-items:center;justify-content:center;background:var(--navy);color:var(--white);font-weight:700;border-radius:30px;text-decoration:none}
.cart-btn{left:162px;top:428px;width:201px;height:52px;font-size:20px;justify-content:flex-start;padding-left:31px;border-radius:30px}
.cart-btn .bubble{position:absolute;right:5px;top:5px;width:42px;height:42px;border-radius:50%;background:var(--white);border:3px solid var(--navy);display:flex;align-items:center;justify-content:center}
.h2{width:1200px;left:0;text-align:center;font-weight:700;font-size:38px}
.center-copy{left:0;width:1200px;text-align:center;color:var(--muted);font-size:11px;line-height:19.5px}
.read-btn{left:540px;top:916px;width:119px;height:38px;font-size:15px}
.disc{border-radius:50%;background:var(--disc);display:flex;align-items:center;justify-content:center}
.product h3{font-size:24px;font-weight:700;margin-bottom:18px}
.product p{font-size:10.5px;line-height:19.5px;color:var(--muted);width:300px}
.price{font-size:24px;font-weight:600;color:var(--navy);margin-top:14px}
.price small{font-size:16px;color:var(--ink);margin-right:4px}
.actions{display:flex;align-items:center;gap:40px;margin-top:28px}
.shop-btn{width:120px;height:38px;font-size:14px}
.add-link{color:var(--navy);font-weight:700;font-size:14px;text-decoration:underline;display:flex;align-items:center;gap:6px}
.side-label{left:71px;top:1690px;transform:translate(-50%,-50%) rotate(-90deg);font-size:36px;font-weight:700;white-space:nowrap}
.client{display:flex;align-items:center;gap:18px}
.avatar-ring{width:88px;height:88px;border-radius:50%;background:var(--white);box-shadow:0 2px 10px rgba(0,0,0,.12);display:flex;align-items:center;justify-content:center}
.avatar{width:76px;height:76px;border-radius:50%;background:linear-gradient(160deg,#c9c3bb,#3c4252)}
.client-name{color:var(--navy);font-weight:600;font-size:16px}
.quote{width:430px;height:144px;background:var(--white);border-radius:4px;box-shadow:0 0 10px rgba(0,0,0,.1);padding:20px 16px;text-align:center;font-style:italic;font-size:11.5px;line-height:19.5px;color:var(--muted)}
.quote::before{content:"";position:absolute;left:48px;top:-16px;border-left:0 solid transparent;border-right:34px solid transparent;border-bottom:16px solid var(--white)}
.dot{width:8px;height:8px;border-radius:50%;background:#d4d7df}
.dot.on{background:var(--navy)}
.field{height:41px;border-radius:22px;background:var(--white);box-shadow:0 0 6px rgba(0,0,0,.08);font-size:11px;color:#555;display:flex;align-items:center;padding-left:26px}
.send-btn{left:792px;top:2978px;width:94px;height:41px;font-size:16px;border:3px solid var(--white)}
.foot-head{color:var(--white);font-weight:600;font-size:16px}
.foot-list{color:#e6e6e6;font-size:10.5px;line-height:19.5px;list-style:none}
.contact-row{display:flex;align-items:flex-start;gap:10px;color:#e6e6e6;font-size:10.5px;line-height:19px}
.social{display:flex;gap:8px}
.social span{width:37px;height:37px;border-radius:50%;background:var(--white)}
.copyright{left:0;top:3488px;width:1200px;height:44px;background:var(--navy);color:#e0e4ee;font-size:10.5px;display:flex;align-items:center;justify-content:center}
</style>
</head>
<body>

<svg class="abs backdrop" width="1200" height="1080" viewBox="0 0 1200 1080" aria-hidden="true">
  <defs>
    <linearGradient id="deck" x1="0" y1="0" x2="1" y2="1">
      <stop offset="0" stop-color="#3a3531"/>
      <stop offset="0.5" stop-color="#4a4540"/>
      <stop offset="1" stop-color="#2b2724"/>
    </linearGradient>
  </defs>
  <path d="M0 640 C200 540 420 560 640 660 C820 740 1000 700 1200 560 V920 C1050 1010 900 1060 700 1050 C450 1030 250 950 0 1030 Z" fill="#eef0f5"/>
  <path d="M0 0 H1200 V470 C1120 610 1000 722 880 722 C760 722 640 650 520 560 C430 490 360 385 250 385 C150 385 60 440 0 495 Z" fill="url(#deck)" role="img" aria-label="Photo of a wooden deck at night"/>
</svg>

<div class="abs brand" style="left:160px;top:40px"><span class="brand-dot"></span>LARKFORGE</div>

<nav class="abs nav" style="left:0;top:0">
  <a style="left:528px;top:48px">Home</a>
  <a style="left:585px;top:48px">About Us</a>
  <a style="left:662px;top:48px">Products</a>
  <a style="left:739px;top:48px">Home Builts</a>
  <a style="left:835px;top:48px">Contact Us</a>
</nav>
<div class="abs nav-icon" style="left:949px;top:38px"><span>
  <svg width="14" height="12" viewBox="0 0 14 12"><path d="M0 1h2.5l2 7h7l1.5-5H4" fill="none" stroke="#4b5a86" stroke-width="1.5"/><circle cx="5.5" cy="10.5" r="1.2" fill="#4b5a86"/><circle cx="10.5" cy="10.5" r="1.2" fill="#4b5a86"/></svg></span></div>
<div class="abs nav-icon" style="left:1001px;top:38px"><span>
  <svg width="12" height="12" viewBox="0 0 12 12"><circle cx="6" cy="3.5" r="3" fill="#4b5a86"/><path d="M0.5 12c0-3.5 2.5-5 5.5-5s5.5 1.5 5.5 5z" fill="#4b5a86"/></svg></span></div>

<h1 class="abs hero-title">Larkforge<br>Outdoor Fire Pit</h1>
<p class="abs hero-copy">Lorem Ipsum is simply dummy text of the printing and typesetting industry. Lorem Ipsum has been the industry's standard dummy text.</p>
<a class="abs btn cart-btn">Add To Cart<span class="bubble">
  <svg width="22" height="18" viewBox="0 0 14 12"><path d="M0 1h2.5l2 7h7l1.5-5H4" fill="none" stroke="#4b5a86" stroke-width="1.5"/><circle cx="5.5" cy="10.5" r="1.2" fill="#4b5a86"/><circle cx="10.5" cy="10.5" r="1.2" fill="#4b5a86"/></svg></span></a>

<svg class="abs" style="left:610px;top:114px" width="526" height="526" viewBox="0 0 526 526">
  <defs>
    <radialGradient id="fire" cx="0.5" cy="0.42" r="0.55">
      <stop offset="0" stop-color="#ffb12a"/>
      <stop offset="0.35" stop-color="#e3541b"/>
      <stop offset="0.65" stop-color="#4e4a4a"/>
      <stop offset="1" stop-color="#2e2b29"/>
    </radialGradient>
  </defs>
  <circle cx="263" cy="263" r="233" fill="url(#fire)" role="img" aria-label="Photo of a lit steel fire pit"/>
  <circle cx="263" cy="263" r="240" fill="none" stroke="#fff" stroke-width="1.5"/>
  <circle cx="263" cy="263" r="254" fill="none" stroke="#fff" stroke-width="1.5"/>
</svg>

<h2 class="abs h2" style="top:734px">About Larkforge</h2>
<p class="abs center-copy" style="top:792px">Lorem Ipsum is simply dummy text of the printing and typesetting industry. Lorem Ipsum has been the<br>industry's standard dummy text ever since the 1500s, when an unknown printer took a galley of type<br>and scrambled it to make a type specimen book. It has survived not only five centuries, but also the leap<br>into electronic typesetting, remaining essentially unchanged.</p>
<a class="abs btn read-btn">Read More</a>

<!-- Products -->
<div class="abs disc" style="left:187px;top:1098px;width:360px;height:360px">
  <div role="img" aria-label="Copper fire pit with mesh dome" style="width:280px;height:170px;border-radius:50% 50% 40% 40%;background:linear-gradient(180deg,#4a3a30,#b8744a 55%,#3a2a22)"></div>
</div>
<div class="abs product" style="left:611px;top:1143px">
  <h3>Steel Cookery</h3>
  <p>Lorem Ipsum is simply dummy text of the printing and typesetting industry. Lorem Ipsum has been the industry's standard dummy text ever since the 1500s, when an unknown printer took a galley of type and scrambled it to make a type specimen book.</p>
  <div class="price"><small>$</small>45.50</div>
  <div class="actions"><a class="btn shop-btn">Shop Now</a><a class="add-link">Add to cart <svg width="16" height="10" viewBox="0 0 16 10"><path d="M0 5h14M10 1l4 4-4 4" fill="none" stroke="#4b5a86" stroke-width="1.4"/></svg></a></div>
</div>

<div class="abs side-label">Larkforge Products</div>

<div class="abs product" style="left:162px;top:1555px">
  <h3>Steel Brackets</h3>
  <p>Lorem Ipsum is simply dummy text of the printing and typesetting industry. Lorem Ipsum has been the industry's standard dummy text ever since the 1500s, when an unknown printer took a galley of type and scrambled it to make a type specimen book.</p>
  <div class="price"><small>$</small>42.90</div>
  <div class="actions"><a class="btn shop-btn">Shop Now</a><a class="add-link">Add to cart <svg width="16" height="10" viewBox="0 0 16 10"><path d="M0 5h14M10 1l4 4-4 4" fill="none" stroke="#4b5a86" stroke-width="1.4"/></svg></a></div>
</div>
<div class="abs disc" style="left:645px;top:1510px;width:360px;height:360px">
  <div role="img" aria-label="Pair of black steel wall brackets" style="width:200px;height:250px;border-radius:12px;background:linear-gradient(135deg,#3a3a3a,#111)"></div>
</div>

<div class="abs disc" style="left:187px;top:1923px;width:360px;height:360px">
  <div role="img" aria-label="Red steel mailbox with a letter" style="width:150px;height:190px;border-radius:30px 30px 8px 8px;background:linear-gradient(160deg,#f04a3a,#b3120e)"></div>
</div>
<div class="abs product" style="left:611px;top:1968px">
  <h3>Steel Mail Boxes</h3>
  <p>Lorem Ipsum is simply dummy text of the printing and typesetting industry. Lorem Ipsum has been the industry's standard dummy text ever since the 1500s, when an unknown printer took a galley of type and scrambled it to make a type specimen book.</p>
  <div class="price"><small>$</small>140.42</div>
  <div class="actions"><a class="btn shop-btn">Shop Now</a><a class="add-link">Add to cart <svg width="16" height="10" viewBox="0 0 16 10"><path d="M0 5h14M10 1l4 4-4 4" fill="none" stroke="#4b5a86" stroke-width="1.4"/></svg></a></div>
</div>

<!-- Success -->
<h2 class="abs h2" style="top:2320px">Our Success</h2>
<p class="abs center-copy" style="top:2372px;font-size:12.5px;line-height:21px">Lorem Ipsum is simply dummy text of the printing and typesetting industry. Lorem<br>Ipsum has been the industry's standard dummy text.</p>

<div class="abs client" style="left:165px;top:2444px"><div class="avatar-ring"><div class="avatar" role="img" aria-label="Client portrait"></div></div><span class="client-name">Client Name</span></div>
<div class="abs quote" style="left:160px;top:2564px">Lorem Ipsum has been the industry's standard dummy text of the printing and typesetting industry. Lorem Ipsum has been the industry's standard dummy text ever since the 1500s, when an unknown printer took a galley of type and scrambled it to make a type specimen book. It has survived not only five centuries, but also the leap into electronic typesetting, remaining essentially unchanged.</div>

<div class="abs client" style="left:615px;top:2444px"><div class="avatar-ring"><div class="avatar" role="img" aria-label="Client portrait"></div></div><span class="client-name">Client Name</span></div>
<div class="abs quote" style="left:610px;top:2564px">Lorem Ipsum has been the industry's standard dummy text of the printing and typesetting industry. Lorem Ipsum has been the industry's standard dummy text ever since the 1500s, when an unknown printer took a galley of type and scrambled it to make a type specimen book. It has survived not only five centuries, but also the leap into electronic typesetting, remaining essentially unchanged.</div>

<div class="abs dot" style="left:558px;top:2750px"></div>
<div class="abs dot on" style="left:595px;top:2750px"></div>
<div class="abs dot" style="left:632px;top:2750px"></div>

<!-- Newsletter + footer -->
<svg class="abs" style="left:0;top:2830px" width="1200" height="660" viewBox="0 0 1200 660" aria-hidden="true">
  <defs>
    <linearGradient id="wall" x1="0" y1="0" x2="1" y2="1">
      <stop offset="0" stop-color="#2d2925"/>
      <stop offset="0.5" stop-color="#3b342b"/>
      <stop offset="1" stop-color="#221f1c"/>
    </linearGradient>
  </defs>
  <rect x="0" y="80" width="1200" height="580" fill="url(#wall)" role="img" aria-label="Dim photo of a vintage mailbox"/>
  <path d="M0 0 H1200 V290 C1120 200 1020 90 880 70 C760 55 660 130 560 210 C470 280 380 410 230 410 C130 410 60 360 0 320 Z" fill="#fff"/>
  <path d="M0 120 C120 70 260 90 380 60 C480 30 560 0 650 20 C760 45 820 70 880 70 C760 60 660 130 560 210 C470 280 380 410 230 410 C130 410 60 360 0 320 Z" fill="#eef0f5"/>
  <path d="M880 70 C1020 90 1120 200 1200 290 V0 C1120 40 1000 80 880 70 Z" fill="#eef0f5"/>
</svg>

<h2 class="abs h2" style="top:2838px;font-size:37px">Subscribe To Our Newsletter</h2>
<p class="abs center-copy" style="top:2890px;font-size:11.5px;line-height:20px;color:#555">Lorem Ipsum is simply dummy text of the printing and typesetting industry. Lorem<br>Ipsum has been the industry's standard dummy text.</p>
<div class="abs field" style="left:315px;top:2978px;width:261px">Enter Name:</div>
<div class="abs field" style="left:587px;top:2978px;width:299px">Enter Email:</div>
<a class="abs btn send-btn">Send</a>

<div class="abs brand" style="left:0;width:1200px;justify-content:center;top:3160px;font-size:28px"><span class="brand-dot"></span>LARKFORGE</div>

<div class="abs foot-head" style="left:163px;top:3267px">Contact Info</div>
<div class="abs contact-row" style="left:163px;top:3320px">
  <svg width="14" height="14" viewBox="0 0 14 14"><path d="M3 1l2.5 3-1.5 1.5c.8 1.8 2.2 3.2 4 4L9.5 8l3 2.5-1.5 2.5C6 13 1 8 1 2.5z" fill="#fff"/></svg>+1-000-000-0000</div>
<div class="abs contact-row" style="left:163px;top:3369px">
  <svg width="14" height="12" viewBox="0 0 14 12"><rect x="0.5" y="1.5" width="13" height="9" fill="none" stroke="#fff"/><path d="M0.5 1.5l6.5 5 6.5-5" fill="none" stroke="#fff"/></svg>info@larkforge.com</div>
<div class="abs contact-row" style="left:163px;top:3410px">
  <svg width="12" height="16" viewBox="0 0 12 16"><path d="M6 15S1 9 1 5.5a5 5 0 0 1 10 0C11 9 6 15 6 15z" fill="none" stroke="#fff" stroke-width="1.3"/><circle cx="6" cy="5.5" r="1.8" fill="#fff"/></svg>100 lorem ispum is simply<br>dummy text.</div>

<div class="abs foot-head" style="left:388px;top:3267px">Quick Links</div>
<ul class="abs foot-list" style="left:388px;top:3320px"><li>Steel Cookery</li><li>Steel Brackets</li><li>Steel Mail Box</li></ul>

<div class="abs foot-head" style="left:613px;top:3267px">Resources</div>
<ul class="abs foot-list" style="left:613px;top:3320px"><li>Terms &amp; Conditions</li><li>Privacy Policy</li><li>Testimonilas</li><li>Newsletter</li><li>About Us</li><li>Contact Us</li></ul>

<div class="abs foot-head" style="left:838px;top:3267px">Follow Us</div>
<div class="abs social" style="left:836px;top:3318px" role="img" aria-label="Social media links"><span></span><span></span><span></span><span></span></div>

<div class="abs copyright">Copyright © 2020 Larkforge. All Rights Reserved.</div>

</body>
</html>
```